Business Card for Coastal Tundrabridge Advisory

We need a business card for Coastal Tundrabridge Advisory. The company website address is provided below. The company logo is attached. We provide specialized permafrost services to the mining, transportation, and oil & gas industries. The card should be prepared for:
Matthias Korhonen, PhD.
Coastal Tundrabridge Advisory
PO Box 418259
Quillwater, Alaska 99642
Direct: +1-907-555-0143
Email: mkorhonen@tundrabridgeadvisory.example
Website: www.coastaltundrabridgeadvisory.example

```html
<!DOCTYPE html>
<html lang="en">
<head>
<meta charset="utf-8">
<title>Coastal Tundrabridge Advisory — Business Card</title>
<link rel="stylesheet" href="https://fonts.googleapis.com/css2?family=Roboto:wght@300;400;500;700&display=swap">
<style>
  :root {
    --backdrop: #1f1f1f;
    --card: #111722;
    --card-edge: #0c1119;
    --ink: #ffffff;
    --ink-soft: #e4e7ec;
    --emboss: #1a2230;
  }
  * { margin: 0; padding: 0; box-sizing: border-box; }
  html, body {
    width: 1200px; height: 780px; overflow: hidden;
    background: var(--backdrop);
    font-family: "Roboto", Arial, sans-serif;
  }
  .stage {
    width: 1200px; height: 780px;
    display: flex; align-items: center; justify-content: center; gap: 40px;
  }
  .card {
    position: relative;
    width: 540px; height: 310px;
    background: var(--card);
    border: 1px solid var(--card-edge);
    color: var(--ink);
    overflow: hidden;
  }

  /* Front */
  .name-block {
    position: absolute; left: 0; top: 34px;
    display: flex; align-items: stretch;
  }
  .name-block .accent {
    width: 14px; background: var(--ink); margin-right: 12px;
  }
  .person-name { font-size: 27px; line-height: 1.05; letter-spacing: 0.2px; }
  .person-name .first { font-weight: 700; }
  .person-name .last { font-weight: 300; }
  .person-title { font-size: 17px; font-weight: 500; margin-top: 4px; }

  .company-name {
    position: absolute; right: 28px; top: 34px;
    text-align: right;
    font-size: 15px; font-weight: 700; letter-spacing: 2.4px; line-height: 1.35;
    color: var(--ink);
  }

  .contacts {
    position: absolute; right: 28px; top: 150px;
    list-style: none; text-align: right;
    font-size: 12px; font-weight: 400; color: var(--ink-soft);
  }
  .contacts li {
    display: flex; align-items: center; justify-content: flex-end; gap: 8px;
    margin-bottom: 7px;
  }
  .contacts svg { width: 13px; height: 13px; flex: none; }

  .address {
    position: absolute; left: 30px; bottom: 28px;
    font-size: 14px; font-weight: 400; line-height: 1.45; color: var(--ink-soft);
    font-style: normal;
  }

  /* Back */
  .emboss-name {
    position: absolute; left: 0; right: 0; top: 80px;
    text-align: center;
    font-size: 30px; font-weight: 700; letter-spacing: 4px; line-height: 1.25;
    color: var(--emboss);
  }
  .services {
    position: absolute; left: 20px; right: 20px; bottom: 34px;
    text-align: center;
  }
  .services h2 {
    font-size: 13px; font-weight: 700; letter-spacing: 0.3px; margin-bottom: 6px;
  }
  .services p { font-size: 11.5px; font-weight: 400; color: var(--ink-soft); }
</style>
</head>
<body>
<main class="stage">

  <section class="card card-front" aria-label="Business card front">
    <div class="name-block">
      <span class="accent"></span>
      <div>
        <h1 class="person-name"><span class="first">Matthias</span> <span class="last">Korhonen</span></h1>
        <p class="person-title">PhD</p>
      </div>
    </div>

    <p class="company-name">COASTAL TUNDRABRIDGE<br>ADVISORY</p>

    <ul class="contacts">
      <li>+1-907-555-0143
        <svg viewBox="0 0 16 16" aria-hidden="true"><circle cx="8" cy="8" r="8" fill="var(--ink)"/><path d="M5.2 4.2l1.6-.3.8 2-1 .8a5.5 5.5 0 0 0 2.7 2.7l.8-1 2 .8-.3 1.6c-3.6.3-6.9-3-6.6-6.6z" fill="var(--card)"/></svg>
      </li>
      <li>mkorhonen@tundrabridgeadvisory.example
        <svg viewBox="0 0 16 16" aria-hidden="true"><circle cx="8" cy="8" r="8" fill="var(--ink)"/><rect x="4" y="5.2" width="8" height="5.6" fill="none" stroke="var(--card)" stroke-width="1.1"/><path d="M4 5.4l4 3 4-3" fill="none" stroke="var(--card)" stroke-width="1.1"/></svg>
      </li>
      <li>www.coastaltundrabridgeadvisory.example
        <svg viewBox="0 0 16 16" aria-hidden="true"><circle cx="8" cy="8" r="8" fill="var(--ink)"/><circle cx="8" cy="8" r="4.2" fill="none" stroke="var(--card)" stroke-width="1"/><ellipse cx="8" cy="8" rx="1.8" ry="4.2" fill="none" stroke="var(--card)" stroke-width="1"/><path d="M3.8 8h8.4" stroke="var(--card)" stroke-width="1"/></svg>
      </li>
    </ul>

    <address class="address">PO Box 418259<br>Quillwater, Alaska 99642</address>
  </section>

  <section class="card card-back" aria-label="Business card back">
    <p class="emboss-name">COASTAL TUNDRABRIDGE<br>ADVISORY</p>
    <div class="services">
      <h2>OUR SERVICES</h2>
      <p>We provide specialized permafrost services to the mining, transportation, and oil &amp; gas industries</p>
    </div>
  </section>

</main>
</body>
</html>
```